Marlow Sail Works President Business Card Carbon fiber catamarans

Hi.. I need a new business card design.. I am the President of a high tech yacht builder. We build Carbon Fiber go fast catamarans... Maybe we use the file I am sharing to you as the back of the card.. We need to look cool and crisp ...

Target Market(s)

Affluent People who will purchase a cool yacht

Industry/Entity Type

Custom Yacht Builder

Contact Information for Business Card

Dean Pellway , President, 731.508.2164 USA

Font styles to use
Serif

Requirements
Must have
• the clean crisp cool feel
Nice to have
• clean and crisp
Should not have
• Bold ugly

```html
<!DOCTYPE html>
<html lang="en">
<head>
<meta charset="utf-8">
<title>Marlow Sail Works – Business Card</title>
<link href="https://fonts.googleapis.com/css2?family=Arimo:wght@400&display=swap" rel="stylesheet">
<style>
  :root {
    --page-bg: #d9dadc;
    --card-dark: #1c1d1f;
    --card-mid: #2a2b2e;
    --weave-light: #3a3b3e;
    --weave-dark: #121314;
    --text-silver: #d6d8db;
    --text-soft: #b9bcc0;
    --divider: #9a9ca0;
  }
  * { margin: 0; padding: 0; box-sizing: border-box; }
  html, body {
    width: 1200px; height: 960px; overflow: hidden;
    background: var(--page-bg);
    font-family: "Arimo", Arial, sans-serif;
  }
  .canvas { position: relative; width: 1200px; height: 960px; }

  .card {
    position: absolute;
    width: 560px; height: 320px;
    border-radius: 4px;
    box-shadow: 0 10px 28px rgba(0,0,0,0.28);
    overflow: hidden;
  }

  /* Front */
  .card--front { left: 90px; top: 120px; }
  .card__weave {
    position: absolute; inset: 0;
    background: radial-gradient(ellipse at 45% 40%, var(--weave-light), var(--weave-dark) 80%);
  }
  .brand {
    position: absolute; left: 0; right: 0; top: 50%;
    transform: translateY(-50%);
    display: flex; align-items: center; justify-content: center; gap: 18px;
  }
  .brand__dot {
    width: 46px; height: 46px; border-radius: 50%;
    background: var(--text-silver);
  }
  .brand__name {
    color: var(--text-silver);
    font-size: 34px; letter-spacing: 6px;
    text-transform: uppercase;
    font-weight: 400;
  }

  /* Back */
  .card--back {
    left: 550px; top: 500px;
    background: linear-gradient(160deg, var(--card-mid), var(--card-dark) 60%);
  }
  .card__mark {
    position: absolute; right: 34px; top: 28px;
    width: 22px; height: 22px; border-radius: 50%;
    background: var(--text-silver);
  }
  .identity {
    position: absolute; right: 296px; top: 128px;
    text-align: right; color: var(--text-silver);
  }
  .identity__name { font-size: 22px; letter-spacing: 1px; text-transform: uppercase; }
  .identity__title { font-size: 12px; color: var(--text-soft); margin-top: 3px; margin-bottom: 12px; }
  .identity__address { font-size: 15px; line-height: 1.3; color: var(--text-soft); }

  .divider {
    position: absolute; left: 278px; top: 118px;
    width: 1px; height: 104px; background: var(--divider);
  }

  .contacts {
    position: absolute; left: 294px; top: 120px;
    list-style: none; color: var(--text-silver);
  }
  .contacts__item {
    display: flex; align-items: center; gap: 10px;
    font-size: 14px; height: 24px;
  }
  .contacts__icon { width: 12px; height: 12px; fill: var(--text-soft); flex: none; }
</style>
</head>
<body>
<main class="canvas">

  <section class="card card--front" aria-label="Card front">
    <div class="card__weave" role="img" aria-label="Carbon fibre weave texture"></div>
    <div class="brand">
      <span class="brand__dot"></span>
      <span class="brand__name">Marlow Sail Works</span>
    </div>
  </section>

  <section class="card card--back" aria-label="Card back">
    <span class="card__mark"></span>

    <div class="identity">
      <p class="identity__name">Dean Pellway</p>
      <p class="identity__title">President</p>
      <p class="identity__address">2216 Keel Point Road<br>Newport, Maine 04953</p>
    </div>

    <div class="divider"></div>

    <ul class="contacts">
      <li class="contacts__item">
        <svg class="contacts__icon" viewBox="0 0 12 12"><path d="M2.5 0.5 L4.5 2.8 L3.4 4.2 Q4.6 6.8 7.8 8.6 L9.2 7.5 L11.5 9.5 L10 11.5 Q4 10.5 0.5 2 Z"/></svg>
        <span>731-508-2164</span>
      </li>
      <li class="contacts__item">
        <svg class="contacts__icon" viewBox="0 0 12 12"><path d="M3 0 H9 V12 H3 Z M4 1.5 V9.5 H8 V1.5 Z"/></svg>
        <span>731-508-2190</span>
      </li>
      <li class="contacts__item">
        <svg class="contacts__icon" viewBox="0 0 12 12"><path d="M0 2.5 H12 V9.5 H0 Z M1 3.5 L6 7 L11 3.5 Z" fill-rule="evenodd"/></svg>
        <span>name@marlowsail.com</span>
      </li>
      <li class="contacts__item">
        <svg class="contacts__icon" viewBox="0 0 12 12"><circle cx="6" cy="6" r="5.5"/></svg>
        <span>www.marlowsail.com</span>
      </li>
    </ul>
  </section>

</main>
</body>
</html>
```